Marwick Law Letterhead

We need a new letterhead design for a Law Firm. The address for the law firm is 1475 Calloway Street, Suite 210, Houston, Texas 77041. Phone Number: 832-361-9027; Fax Number: 832-614-7359. The logo is uploaded to the project.

```html
<!DOCTYPE html>
<html lang="en">
<head>
<meta charset="utf-8">
<title>Marwick Law Letterhead</title>
<link rel="stylesheet" href="https://fonts.googleapis.com/css2?family=Montserrat:wght@400;500;600&display=swap">
<style>
  :root {
    --navy: #1b2f5e;
    --red: #d01c2a;
    --red-dark: #8e0f1a;
    --ink: #1c1c1f;
    --paper: #ffffff;
    --backdrop: #e6e6e8;
  }
  * { box-sizing: border-box; margin: 0; padding: 0; }
  html, body {
    width: 1200px; height: 960px; overflow: hidden;
    background: var(--backdrop);
    font-family: "Montserrat", sans-serif;
  }
  .letterhead {
    position: absolute; left: 275px; top: 20px;
    width: 650px; height: 920px;
    background: var(--paper);
    box-shadow: 0 4px 18px rgba(0,0,0,.12);
    overflow: hidden;
  }
  .header-band { position: absolute; left: 0; top: 0; }
  .contact {
    position: absolute; left: 470px; top: 26px;
    color: #fff; font-size: 10.5px; line-height: 14px; font-weight: 500;
    font-style: normal;
  }
  .contact-line { display: flex; align-items: center; gap: 6px; }
  .contact-line svg { width: 10px; height: 10px; fill: #fff; }
  .firm-name {
    position: absolute; left: 42px; top: 46px;
    color: var(--navy); font-size: 30px; font-weight: 600; letter-spacing: 1px;
    display: flex; align-items: center; gap: 12px;
  }
  .firm-mark { width: 30px; height: 30px; background: var(--navy); }
  .letter {
    position: absolute; left: 42px; top: 200px; width: 570px;
    color: var(--ink); font-size: 11.5px; line-height: 17px;
  }
  .recipient { margin-bottom: 2px; }
  .letter p { margin-bottom: 17px; }
  .closing { margin-top: 4px; font-size: 13px; font-weight: 500; }
  .signature {
    width: 110px; height: 34px; margin-top: 6px;
    background: linear-gradient(90deg, #dcdcdf, #f1f1f3);
    border-radius: 3px;
  }
  .footer-band { position: absolute; left: 0; bottom: 0; }
  .website {
    position: absolute; left: 428px; bottom: 44px;
    color: #fff; font-size: 10.5px; line-height: 14px; font-weight: 500;
    display: flex; align-items: center; gap: 6px; white-space: nowrap;
  }
  .website svg { width: 11px; height: 11px; }
</style>
</head>
<body>
<main class="letterhead">
  <svg class="header-band" width="650" height="150" viewBox="0 0 650 150">
    <defs>
      <linearGradient id="redFade" x1="0" x2="1">
        <stop offset="0" stop-color="var(--red)"/>
        <stop offset="1" stop-color="var(--red-dark)"/>
      </linearGradient>
    </defs>
    <polygon points="325,0 650,0 650,128 442,134" fill="var(--navy)"/>
    <polygon points="325,0 442,134 442,139 320,0" fill="url(#redFade)"/>
  </svg>

  <address class="contact">
    <div>1475 Calloway Street,</div>
    <div>Suite 210, Houston,</div>
    <div>Texas 77041</div>
    <div class="contact-line">
      <svg viewBox="0 0 24 24"><path d="M6.6 10.8a15 15 0 0 0 6.6 6.6l2.2-2.2a1 1 0 0 1 1-.25 11.4 11.4 0 0 0 3.6.57 1 1 0 0 1 1 1V20a1 1 0 0 1-1 1A17 17 0 0 1 3 4a1 1 0 0 1 1-1h3.5a1 1 0 0 1 1 1c0 1.25.2 2.45.57 3.570a1 1 0 0 1-.25 1z"/></svg>
      832-361-9027
    </div>
    <div class="contact-line">
      <svg viewBox="0 0 24 24"><path d="M6 2h9l3 3v4H6zM4 10h16a2 2 0 0 1 2 2v6h-4v4H6v-4H2v-6a2 2 0 0 1 2-2zm4 7v3h8v-3z"/></svg>
      832-614-7359
    </div>
  </address>

  <div class="firm-name"><span class="firm-mark"></span>Marwick Law</div>

  <section class="letter">
    <div class="recipient">Mr/s<br>First Name and Last Name<br>Company Name<br>Address</div>
    <p>Lorem ipsum dolor sit amet,consectetur adipiscing sed do eiusmod tempor incididunt laboreet dolore magna aliqua.Ut enim ad minim.veniam, quis nostrud exercitation ullamco laboris nisi ut aliquip exea commodo consequat.Lorem ipsum dolor sit amet,consectetur adipiscing sed do eiusmod tempor incididunt.labore et dolore magna aliqua. Ut enim</p>
    <p>Lorem ipsum dolor sit amet, consectetur adipiscing sed do eiusmod tempor incididunt labore et dolore magna aliqua. Ut enim ad minim veniam, quis nostrud exercitation ullamco laboris nisi ut aliquip exea commodo consequat.Duis aute irure dolor in reprehenderit in voluptate velit esse cillum irure dolor in reprehenderit in voluptate velit esse irure</p>
    <p>Lorem ipsum dolor sit amet, consectetur adipiscing sed do eiusmod tempor incididunt labore et dolore magna aliqua. consequat. Duis aute irure dolor in.reprehenderit in voluptate velit esse cillum dolore eu fugiat nulla pariatur. Excepteur sint occaecat cupidatat non proident, sunt in culpa qui officia deserunt mollit,</p>
    <p>Lorem ipsum dolor sit amet, consectetur adipiscing sed do eiusmod tempor incididunt labore et dolore magna aliqua. Ut enim Lorem ipsum dolor sit amet, consectetur adipiscing sed do eiusmod tempor incididunt labore et dolore magna aliqua. Ut enim Lorem ipsum aliqua.ipsum</p>
    <p>Lorem ipsum dolor sit amet, consectetur adipiscing sed do eiusmod tempor incididunt labore et dolore magna aliqua. Ut enim ad minim veniam, quis nostrud exercitation ullamco laboris nisi ut aliquip exea commodo consequat.Duis aute irure dolor in reprehenderit in voluptate velit esse cillum irure dolor in reprehenderit in voluptate velit esse irure</p>
    <p>Lorem ipsum dolor sit amet, consectetur adipiscing sed do eiusmod tempor incididunt labore et dolore magna aliqua. Ut enim ad minim veniam, quis nostrud exercitation ullamco laboris nisi ut aliquip exea commodo consequat.Duis aute irure dolor in reprehenderit in voluptate velit esse cillum irure dolor in reprehenderit in voluptate velit esse irure</p>
    <div class="closing">Regards</div>
    <div class="signature" role="img" aria-label="Handwritten signature of the sender"></div>
  </section>

  <svg class="footer-band" width="650" height="100" viewBox="0 0 650 100">
    <defs>
      <linearGradient id="redBox" x1="0" x2="1">
        <stop offset="0" stop-color="var(--red)"/>
        <stop offset="1" stop-color="var(--red-dark)"/>
      </linearGradient>
    </defs>
    <polygon points="0,50 404,50 386,82 0,82" fill="var(--navy)"/>
    <polygon points="430,24 612,24 580,82 398,82" fill="url(#redBox)"/>
    <polygon points="632,24 650,24 650,62 611,62" fill="var(--navy)"/>
  </svg>
  <div class="website">
    <svg viewBox="0 0 24 24"><circle cx="12" cy="12" r="10" fill="#fff"/><path d="M2 12h20M12 2a15 15 0 0 1 0 20M12 2a15 15 0 0 0 0 20" stroke="var(--red)" stroke-width="1.8" fill="none"/></svg>
    www.marwicklaw.com
  </div>
</main>
</body>
</html>
```